RTavenor Business Cards & Letterhead

I have a logo but need a design for some new business cards. We are a Design-Build Firm that specializes in the design and construction of commercial projects.
the cards need to be professional. no cartoon stuff.
i would like to have the cards in AI format so I can update the card as needed. Logo is provided.
Our Address is: 4187 Marlowe Ct. Linden Falls, Vermont 27614

```html
<!DOCTYPE html>
<html lang="en">
<head>
<meta charset="UTF-8">
<title>RTavenor Business Cards</title>
<link href="https://fonts.googleapis.com/css2?family=Open+Sans:wght@400;600;700;800&display=swap" rel="stylesheet">
<style>
  :root {
    --page-bg: #2c2c31;
    --card-dark: #1f1f24;
    --blue-light: #1f86cf;
    --blue-deep: #0b4576;
    --brand-blue: #1a73bd;
    --wordmark-grey: #8a8b90;
    --text-white: #f2f3f5;
    --divider: #9a9ca3;
  }
  * { margin: 0; padding: 0; box-sizing: border-box; }
  html, body { width: 1200px; height: 780px; overflow: hidden; }
  body {
    background: var(--page-bg);
    font-family: "Open Sans", Arial, sans-serif;
    display: flex;
    flex-direction: column;
    align-items: center;
    justify-content: center;
    gap: 30px;
  }
  .card {
    position: relative;
    width: 600px;
    height: 343px;
    border-radius: 22px;
    overflow: hidden;
    box-shadow: 0 14px 30px rgba(0,0,0,0.45);
  }
  .card-bg { position: absolute; inset: 0; width: 100%; height: 100%; }

  .front-brand {
    position: absolute;
    inset: 0;
    display: flex;
    align-items: center;
    justify-content: center;
    gap: 14px;
  }
  .brand-square { width: 34px; height: 34px; background: var(--brand-blue); }
  .brand-name {
    font-weight: 800;
    font-size: 52px;
    letter-spacing: 1px;
    color: var(--wordmark-grey);
    line-height: 1;
  }

  .back-mark {
    position: absolute;
    left: 118px; top: 108px;
    width: 118px; height: 118px;
    background: var(--brand-blue);
  }
  .back-divider {
    position: absolute;
    left: 270px; top: 84px;
    width: 1px; height: 150px;
    background: var(--divider);
  }
  .contact-block {
    position: absolute;
    left: 292px; top: 88px;
    color: var(--text-white);
  }
  .person-name {
    font-weight: 700;
    font-size: 23px;
    color: var(--brand-blue);
    letter-spacing: 0.5px;
    line-height: 1.1;
  }
  .person-title { font-weight: 600; font-size: 14px; margin-top: 3px; }
  .contact-list {
    list-style: none;
    margin-top: 18px;
    font-size: 13px;
    line-height: 1.55;
  }
  .contact-list li { display: flex; align-items: center; gap: 8px; }
  .contact-icon { width: 12px; height: 12px; flex: none; }
  .address {
    position: absolute;
    left: 118px; bottom: 36px;
    color: var(--text-white);
    font-size: 15px;
    letter-spacing: 0.2px;
  }
</style>
</head>
<body>

  <section class="card card-front">
    <svg class="card-bg" viewBox="0 0 600 343" preserveAspectRatio="none">
      <defs>
        <linearGradient id="blueFront" x1="0" y1="0" x2="1" y2="1">
          <stop offset="0" stop-color="var(--blue-light)"/>
          <stop offset="1" stop-color="var(--blue-deep)"/>
        </linearGradient>
      </defs>
      <rect width="600" height="343" fill="url(#blueFront)"/>
      <path d="M75,0 H520 C585,90 590,250 540,343 H110 C40,260 30,110 75,0 Z" fill="var(--card-dark)"/>
    </svg>
    <div class="front-brand">
      <span class="brand-square"></span>
      <span class="brand-name">RTAVENOR</span>
    </div>
  </section>

  <section class="card card-back">
    <svg class="card-bg" viewBox="0 0 600 343" preserveAspectRatio="none">
      <defs>
        <linearGradient id="blueBack" x1="0" y1="0" x2="1" y2="1">
          <stop offset="0" stop-color="var(--blue-light)"/>
          <stop offset="1" stop-color="var(--blue-deep)"/>
        </linearGradient>
      </defs>
      <rect width="600" height="343" fill="url(#blueBack)"/>
      <path d="M75,0 H520 C585,90 590,250 540,343 H110 C40,260 30,110 75,0 Z" fill="var(--card-dark)"/>
    </svg>

    <div class="back-mark"></div>
    <div class="back-divider"></div>

    <div class="contact-block">
      <h1 class="person-name">MARCUS TAVENOR</h1>
      <p class="person-title">Founder/President</p>
      <ul class="contact-list">
        <li>
          <svg class="contact-icon" viewBox="0 0 12 12"><path d="M2.5 1 L4.5 1 L5.3 3.4 L4 4.4 C4.6 5.8 6.2 7.4 7.6 8 L8.6 6.7 L11 7.5 L11 9.5 C11 10.3 10.3 11 9.5 11 C5 11 1 7 1 2.5 C1 1.7 1.7 1 2.5 1 Z" fill="var(--brand-blue)"/></svg>
          <span>(555) 214-0148</span>
        </li>
        <li>
          <svg class="contact-icon" viewBox="0 0 12 12"><circle cx="6" cy="6" r="5" fill="none" stroke="var(--brand-blue)" stroke-width="1.3"/><ellipse cx="6" cy="6" rx="2.2" ry="5" fill="none" stroke="var(--brand-blue)" stroke-width="1"/><line x1="1" y1="6" x2="11" y2="6" stroke="var(--brand-blue)" stroke-width="1"/></svg>
          <span>www.rtavenor.com</span>
        </li>
        <li>
          <svg class="contact-icon" viewBox="0 0 12 12"><rect x="1" y="2.5" width="10" height="7" rx="1" fill="var(--brand-blue)"/><polyline points="1.5,3 6,6.5 10.5,3" fill="none" stroke="var(--card-dark)" stroke-width="1"/></svg>
          <span>MRT@RTavenor.com</span>
        </li>
      </ul>
    </div>

    <p class="address">4187 Marlowe Ct. Linden Falls, Vermont 27614</p>
  </section>

</body>
</html>
```